Business Card for a New Zealand IT Startup

I need a business card for VELTA Holdings. We are a young startup based in New Zealand working in internet marketing and web development. The design should have some element connected to New Zealand, such as wave, koru or silver fern, just don't use a kiwi bird.

```html
<!DOCTYPE html>
<html lang="en">
<head>
<meta charset="utf-8">
<title>VELTA Holdings – Business Card</title>
<link href="https://fonts.googleapis.com/css2?family=Roboto:wght@400;500;700&display=swap" rel="stylesheet">
<style>
  :root {
    --brand-blue: #0270b9;
    --brand-orange: #f15a24;
    --paper: #ffffff;
    --backdrop: #262626;
    --ink-light: #ffffff;
  }
  * { margin: 0; padding: 0; box-sizing: border-box; }
  html, body {
    width: 1125px;
    height: 1200px;
    overflow: hidden;
    background: var(--backdrop);
    font-family: "Roboto", Arial, sans-serif;
  }
  .card {
    position: absolute;
    left: 150px;
    width: 825px;
    height: 470px;
    border-radius: 30px;
    overflow: hidden;
  }
  .card-front { top: 98px; background: var(--paper); }
  .card-back  { top: 630px; background: var(--brand-orange); }

  .wave-art { position: absolute; inset: 0; width: 100%; height: 100%; }

  .brand-name {
    position: absolute;
    left: 64px;
    top: 95px;
    display: flex;
    align-items: center;
    gap: 16px;
    font-weight: 700;
    font-size: 56px;
    letter-spacing: 0.01em;
    color: var(--brand-blue);
  }
  .brand-dot {
    width: 30px; height: 30px;
    border-radius: 50%;
    background: var(--brand-orange);
  }

  .contact-block {
    position: absolute;
    right: 41px;
    top: 218px;
    text-align: right;
    color: var(--ink-light);
  }
  .person-name { font-weight: 700; font-size: 29px; line-height: 32px; letter-spacing: 0.01em; }
  .person-role { font-weight: 500; font-size: 19px; line-height: 24px; }
  .address { margin-top: 16px; font-size: 19px; line-height: 25px; }
  .contact-list { list-style: none; margin-top: 12px; font-size: 19px; line-height: 26px; }
  .contact-list li { display: flex; justify-content: flex-end; align-items: center; gap: 8px; }
  .contact-icon { width: 18px; height: 18px; flex: none; }

  .back-brand {
    position: absolute;
    left: 0; right: 0; top: 190px;
    display: flex; justify-content: center; align-items: center; gap: 18px;
    font-weight: 700;
    font-size: 60px;
    color: var(--ink-light);
  }
  .back-brand .brand-dot { width: 36px; height: 36px; background: var(--ink-light); }
  .back-url {
    position: absolute;
    left: 0; right: 0; top: 390px;
    text-align: center;
    font-size: 19px;
    letter-spacing: 0.38em;
    color: var(--ink-light);
  }
</style>
</head>
<body>
  <section class="card card-front">
    <svg class="wave-art" viewBox="0 0 800 455" preserveAspectRatio="none" aria-hidden="true">
      <path fill="#f15a24" d="M25,350 C80,428 150,442 212,434 C340,420 462,290 562,184 C640,104 700,68 745,50 L800,38 L800,455 L0,455 Z"/>
      <path fill="#0270b9" stroke="#ffffff" stroke-width="3" d="M0,318 C60,420 150,452 220,446 C360,436 482,302 582,192 C662,106 740,42 802,34 L802,457 L-2,457 Z"/>
    </svg>

    <div class="brand-name"><span>VELTA Holdings</span><span class="brand-dot"></span></div>

    <div class="contact-block">
      <p class="person-name">MARA QUINN</p>
      <p class="person-role">CEO/FOUNDER</p>
      <p class="address">214 Harbour Terrace<br>Wellington, NZ 6011</p>
      <ul class="contact-list">
        <li>021 555 0148
          <svg class="contact-icon" viewBox="0 0 24 24"><path fill="#fff" d="M6.6 10.8a15.1 15.1 0 0 0 6.6 6.6l2.2-2.2a1 1 0 0 1 1-.25 11.4 11.4 0 0 0 3.6.57 1 1 0 0 1 1 1V20a1 1 0 0 1-1 1A17 17 0 0 1 3 4a1 1 0 0 1 1-1h3.5a1 1 0 0 1 1 1c0 1.25.2 2.46.57 3.6a1 1 0 0 1-.25 1z"/></svg>
        </li>
        <li>mara@veltaholdings.com
          <svg class="contact-icon" viewBox="0 0 24 24"><rect x="2" y="5" width="20" height="14" rx="1" fill="#fff"/><path d="M3 6l9 7 9-7" fill="none" stroke="#0270b9" stroke-width="1.6"/></svg>
        </li>
        <li>www.veltaholdings.com
          <svg class="contact-icon" viewBox="0 0 24 24"><circle cx="12" cy="12" r="10" fill="#fff"/><path d="M2 12h20M12 2c3 3 3 17 0 20M12 2c-3 3-3 17 0 20" fill="none" stroke="#0270b9" stroke-width="1.4"/></svg>
        </li>
      </ul>
    </div>
  </section>

  <section class="card card-back">
    <div class="back-brand"><span class="brand-dot"></span><span>VELTA Holdings</span></div>
    <p class="back-url">www.veltaholdings.com</p>
  </section>
</body>
</html>
```